Very new and innovative Web design for Property managers of Vacation rentals

We are looking for a new website design for travel agencies and property managers specialised on vacation rentals business, holiday villas and apartments.

The end users of this website are travellers who are looking for a vacation home for their next holiday: this is the reason why the website must be easy to use, attractive, professional, possibly elegant and focused on get new reservations.

This is a draft of our current website: https://intro3.kelumsito.com/
Please consider that we would like to have proposals with a totally different and innovative layout, surprise us!

These are the pages of the website:
• Homepage: feel free to redesign all the homepage as you wish, surprise us with something very new! Please consider that Property manager/Travel agencies usually want to have the opportunity to put in evidence groups of houses with specific characteristics (eg. villas with private swimming pool, apartment in big/small towns, villas with air co, etc…), destinations and tourist areas, and sometimes experiences or activities (please consider that the website layout must be suitable even if some of the previous sections are not used).
• Search page: we’d like to organise the results of the search page in three different ways:
o Grid
o Map
o List
• Property page: to illustrate the characteristics, descriptions, images, …. of the property. It is very important to put in evidence images of the property and to maintain the booking form (and the other call to action bottom – eg. whatsapp) always visible
• Custom pages: static pages composed usually by text, images and call to actions
• Contact us (general form)
• Info request (specific of a property form)
• Booking process
• Blog, organised in four pages:
o Home Page – introduction to the blog
o List of articles
o Single article
o Site Map (presentation of categories and sub-categories)

If possible, we’d prefer to receive the material in Adobe XD or similar so that we can obtain the three versions:
- smartphone
- tablet
- desktop

The website will be then developed in Bootstrap: as a result we’ll need the icons in SVG format (or the library used)

In attachment you can find the map of the website pages

```html
<!DOCTYPE html>
<html lang="en">
<head>
<meta charset="utf-8">
<title>Tripnesta — Explore the Beauty of Italy</title>
<link href="https://fonts.googleapis.com/css2?family=Merriweather:ital,wght@0,300;0,400;0,700;0,900;1,400&family=Mulish:wght@400;600;700&display=swap" rel="stylesheet">
<style>
:root{
  --orange:#f2541b;
  --orange-soft:#f07a4a;
  --ink:#2b2b2b;
  --muted:#777;
  --line:#e6e6e6;
  --dark:#2f2f2f;
  --blue:#6e9fd6;
  --white:#fff;
}
*{box-sizing:border-box;margin:0;padding:0}
html,body{width:1200px;height:2774px;overflow:hidden}
body{position:relative;background:var(--white);font-family:'Mulish',sans-serif;color:var(--ink)}
.abs{position:absolute}
.serif{font-family:'Merriweather',serif}

/* hero */
.hero{left:0;top:0;width:1200px;height:584px;background:linear-gradient(100deg,#6f9fd8 0%,#b49bb4 35%,#e57a55 65%,#e0693e 100%)}
.nav{left:0;top:0;width:1200px;height:66px;border-bottom:1px solid rgba(255,255,255,.25)}
.brand{left:151px;top:18px;display:flex;align-items:center;gap:8px;color:#fff;font-weight:700;font-size:21px;letter-spacing:.5px}
.brand i{width:22px;height:22px;background:var(--orange);display:block}
.menu{left:404px;top:23px;display:flex;gap:34px;color:#fff;font-size:13.5px;font-weight:700}
.menu .active{color:var(--orange)}
.btn-login{left:856px;top:13px;width:84px;height:38px;border:1px solid #fff;border-radius:20px;color:#fff;font-size:13.5px;font-weight:700;display:flex;align-items:center;justify-content:center}
.btn-sign{left:965px;top:13px;width:84px;height:38px;background:#fff;border-radius:20px;color:var(--orange);font-size:13.5px;font-weight:700;display:flex;align-items:center;justify-content:center}
.hero-title{left:148px;top:220px;font-family:'Merriweather',serif;font-weight:900;font-size:80px;color:var(--orange);line-height:1}
.hero-sub{left:150px;top:310px;font-family:'Merriweather',serif;font-weight:300;font-size:32px;color:#fff}
.hero-sub b{font-weight:900}

/* search */
.search{left:151px;top:523px;width:898px;height:112px;background:#fff;border-radius:6px;box-shadow:0 4px 18px rgba(0,0,0,.1)}
.field{position:absolute;top:28px;height:52px;border:1.5px solid #eee;border-radius:6px;box-shadow:0 2px 4px rgba(242,84,27,.25);display:flex;align-items:center;justify-content:space-between;padding:0 18px 0 22px;color:#999;font-size:13px}
.field svg{flex:none}
.f-dest{left:26px;width:236px}
.f-in{left:278px;width:152px;top:33px;height:46px}
.f-out{left:446px;width:152px;top:33px;height:46px}
.f-trav{left:615px;width:152px;top:34px;height:46px}
.submit{position:absolute;left:779px;top:38px;width:98px;height:37px;background:var(--orange);color:#fff;font-weight:700;font-size:13.5px;border-radius:4px;display:flex;align-items:center;justify-content:center}

/* section heading */
.sh{position:absolute}
.sh h2{font-family:'Merriweather',serif;font-weight:400;font-size:42px;color:var(--ink);line-height:1.2;white-space:nowrap}
.sh .rule{height:2px;background:var(--orange);position:relative;margin-top:1px}
.sh .rule::before{content:"";position:absolute;left:0;top:-3px;width:8px;height:8px;border-radius:50%;background:var(--orange)}
.sh em{display:block;font-family:'Merriweather',serif;font-style:italic;font-size:11.5px;color:#444;margin-top:2px}

/* destination cards */
.dest{top:769px;width:208px;height:300px;border-radius:4px;overflow:hidden;box-shadow:0 4px 10px rgba(0,0,0,.15)}
.dest .photo{width:100%;height:100%}
.dest .cap{position:absolute;left:0;bottom:0;width:100%;height:74px;background:rgba(236,110,60,.85);text-align:center;color:#fff;padding-top:6px}
.dest .cap strong{display:block;font-family:'Merriweather',serif;font-weight:900;font-size:24px}
.dest .cap span{font-family:'Merriweather',serif;font-size:16px}

.btn{display:flex;align-items:center;justify-content:center;font-weight:700;font-size:14.5px;border-radius:4px}
.btn-fill{background:var(--orange);color:#fff;box-shadow:0 4px 10px rgba(242,84,27,.3)}
.btn-line{border:2px solid var(--orange);color:var(--orange);background:#fff}

/* features */
.feat-icon{top:1296px;width:90px;height:90px;border-radius:4px;background:#f3f3f3;box-shadow:0 4px 8px rgba(0,0,0,.12);display:flex;align-items:center;justify-content:center}
.feat-icon.hot{background:linear-gradient(135deg,#f0541b,#f5855a)}
.feat-label{top:1412px;width:240px;text-align:center;font-size:14.5px;font-weight:600;color:var(--ink)}

/* arrows */
.arrow{width:40px;height:40px;border-radius:3px;display:flex;align-items:center;justify-content:center;color:#fff;font-size:18px}
.arrow.prev{background:var(--dark)}
.arrow.next{background:var(--orange)}

/* villas */
.villa{top:1673px;width:273px;height:350px;background:#fff;box-shadow:0 3px 10px rgba(0,0,0,.12)}
.villa .photo{height:203px;width:100%}
.villa .body{padding:8px 12px 0}
.villa h3{font-family:'Merriweather',serif;font-weight:400;font-size:16px}
.villa .loc{font-family:'Merriweather',serif;font-size:10.5px;color:#888;margin-top:2px}
.villa .rate{display:flex;justify-content:space-between;align-items:center;margin-top:4px}
.villa .stars{color:var(--orange);font-size:22px;letter-spacing:1px}
.villa .stars s{text-decoration:none;color:#ddd}
.villa .rev{font-family:'Merriweather',serif;font-size:10px;color:#888}
.villa .desc{font-family:'Merriweather',serif;font-size:11px;color:#555;margin-top:2px}
.villa .more{margin:10px auto 0;width:80px;height:20px;background:var(--orange);color:#fff;border-radius:4px;font-family:'Merriweather',serif;font-size:8.5px;display:flex;align-items:center;justify-content:center}
.villa .specs{position:absolute;left:0;bottom:0;width:100%;height:26px;border-top:1px solid var(--line);display:flex;justify-content:space-around;align-items:center;font-family:'Merriweather',serif;font-size:8.5px;color:#666}

/* testimonials */
.quote-deco{left:470px;top:2078px;font-family:'Merriweather',serif;font-weight:900;font-size:220px;line-height:1;color:#fde9e2;letter-spacing:40px}
.tbox{top:2203px;width:430px;height:130px;border:1.5px solid #f2a98b;border-radius:8px;background:#fff;box-shadow:0 2px 6px rgba(242,84,27,.15);padding:44px 36px 0;text-align:center;font-family:'Merriweather',serif;font-style:italic;font-size:10.5px;line-height:18px;color:#444}
.avatar{width:78px;height:78px;border-radius:50%;border:2px solid var(--orange)}

/* newsletter */
.footer-band{left:0;top:2448px;width:1200px;height:304px;background:linear-gradient(100deg,#6f9fd8 0%,#b49bb4 40%,#e57a55 75%,#e0693e 100%)}
.news{left:150px;top:2389px;width:899px;height:113px;background:#fff;border-radius:4px;box-shadow:0 4px 14px rgba(0,0,0,.1)}
.news h4{position:absolute;left:57px;top:40px;font-family:'Merriweather',serif;font-weight:400;font-size:24px}
.news .email{position:absolute;left:425px;top:25px;width:295px;height:63px;border:1.5px solid #eee;box-shadow:0 2px 4px rgba(242,84,27,.2);color:#aaa;font-size:14px;display:flex;align-items:center;padding-left:17px}
.news .submit{left:752px;top:34px;width:118px;height:42px;font-size:14.5px}

.fcol{top:2536px;color:#fff}
.fcol h5{font-size:22px;font-weight:700;margin-bottom:28px}
.fcol h5.light{font-weight:400}
.fcol ul{list-style:none}
.fcol li{font-size:14px;font-weight:600;height:45px;display:flex;align-items:flex-start;gap:8px}
.fcol li .sq{width:24px;height:24px;background:#fff;border-radius:4px;flex:none;margin-top:-4px}
.fcol li.hl{color:var(--orange)}
.fcol.contact li{font-size:14.5px;line-height:15px}
.copyright{left:0;top:2754px;width:1200px;text-align:center;font-size:7.5px;color:#999}
</style>
</head>
<body>

<div class="abs hero" role="img" aria-label="Aerial photo of a historic Italian city by the water with a domed basilica, tinted blue to orange"></div>

<header class="abs nav">
  <div class="abs brand"><i></i>TRIPNESTA</div>
  <nav class="abs menu">
    <span>Last Minute</span><span class="active">Special Offers</span><span>Experience</span><span>Contact Us</span>
  </nav>
  <div class="abs btn-login">Login</div>
  <div class="abs btn-sign">Sign Up</div>
</header>

<div class="abs hero-title">Explore</div>
<div class="abs hero-sub">The Beauty of &nbsp;<b>Italy</b></div>

<form class="abs search">
  <div class="field f-dest">Destination
    <svg width="20" height="26" viewBox="0 0 20 26"><path d="M10 1a8.5 8.5 0 0 0-8.5 8.5C1.5 16 10 25 10 25s8.5-9 8.5-15.5A8.5 8.5 0 0 0 10 1z" fill="#999"/><circle cx="10" cy="9.5" r="3.3" fill="#fff"/></svg></div>
  <div class="field f-in">Check in
    <svg width="24" height="20" viewBox="0 0 24 20"><rect x="1" y="3" width="22" height="16" rx="2" fill="#999"/><g fill="#fff"><rect x="4" y="8" width="3" height="2"/><rect x="9" y="8" width="3" height="2"/><rect x="14" y="8" width="3" height="2"/><rect x="4" y="12" width="3" height="2"/><rect x="9" y="12" width="3" height="2"/><rect x="14" y="12" width="3" height="2"/></g></svg></div>
  <div class="field f-out">Check out
    <svg width="24" height="20" viewBox="0 0 24 20"><rect x="1" y="3" width="22" height="16" rx="2" fill="#999"/><g fill="#fff"><rect x="4" y="8" width="3" height="2"/><rect x="9" y="8" width="3" height="2"/><rect x="14" y="8" width="3" height="2"/><rect x="4" y="12" width="3" height="2"/><rect x="9" y="12" width="3" height="2"/><rect x="14" y="12" width="3" height="2"/></g></svg></div>
  <div class="field f-trav">Travellers
    <svg width="24" height="18" viewBox="0 0 24 18"><g fill="#999"><circle cx="12" cy="5" r="4"/><path d="M4 18c0-5 3.5-7 8-7s8 2 8 7z"/><circle cx="4.5" cy="7" r="2.7"/><circle cx="19.5" cy="7" r="2.7"/></g></svg></div>
  <div class="submit">Submit</div>
</form>

<div class="sh" style="left:147px;top:664px">
  <h2>Discover Popular Destinations</h2>
  <div class="rule" style="margin-left:282px;width:284px"></div>
  <em style="margin-left:307px">Explore the Best of the World</em>
</div>

<div class="abs dest" style="left:147px"><div class="photo" role="img" aria-label="Photo of a narrow old stone alley with baroque buildings" style="background:linear-gradient(180deg,#8a8a90 0%,#b89460 45%,#8f6a3e 100%)"></div><div class="cap"><strong>Alley Road</strong><span>Patch City</span></div></div>
<div class="abs dest" style="left:380px"><div class="photo" role="img" aria-label="Photo of colourful sea houses on a cliff" style="background:linear-gradient(180deg,#9cc0d8 0%,#d98a70 40%,#5d6f5c 100%)"></div><div class="cap"><strong>Sea Houses</strong><span>Positano</span></div></div>
<div class="abs dest" style="left:612px"><div class="photo" role="img" aria-label="Photo of an alpine lake with autumn trees and mountains" style="background:linear-gradient(180deg,#8fb2d8 0%,#c9a07a 50%,#4f6a7e 100%)"></div><div class="cap"><strong>Dolomites</strong><span>Mountains</span></div></div>
<div class="abs dest" style="left:845px"><div class="photo" role="img" aria-label="Photo of an ancient amphitheatre under a bright sky" style="background:linear-gradient(180deg,#4e8fa0 0%,#e0c58e 45%,#9a6a3e 100%)"></div><div class="cap"><strong>Colosseum</strong><span>World’s Wonder</span></div></div>

<div class="abs btn btn-fill" style="left:525px;top:1108px;width:150px;height:52px">Explore More</div>

<div class="sh" style="left:147px;top:1191px">
  <h2>Why choose us?</h2>
  <div class="rule" style="margin-left:170px;width:265px"></div>
  <em style="margin-left:175px;font-size:11px">Creating Best Experiences</em>
</div>

<div class="abs feat-icon" style="left:230px">
  <svg width="36" height="40" viewBox="0 0 36 40"><path d="M6 4l8-2 4 6 8 8 6 2-1 4-6-2 2 6-3 6-3-2 1-6-5-6-7-5z" fill="var(--orange)"/><circle cx="16" cy="35" r="3" fill="var(--orange)"/></svg>
</div>
<div class="abs feat-icon hot" style="left:559px">
  <svg width="40" height="40" viewBox="0 0 40 40"><path d="M22 4h14v14L18 36 4 22z" fill="#fff"/><circle cx="30" cy="10" r="2.5" fill="var(--orange)"/><path d="M14 24l10-10" stroke="var(--orange)" stroke-width="2"/><circle cx="15" cy="17" r="2" fill="var(--orange)"/><circle cx="22" cy="22" r="2" fill="var(--orange)"/></svg>
</div>
<div class="abs feat-icon" style="left:887px">
  <svg width="40" height="40" viewBox="0 0 40 40"><circle cx="18" cy="13" r="8" fill="var(--orange)"/><path d="M4 38c0-9 6-14 14-14s14 5 14 14z" fill="var(--orange)"/><path d="M31 26l7 4-7 4z" fill="var(--orange)"/></svg>
</div>
<div class="abs feat-label" style="left:157px">Wide Connections</div>
<div class="abs feat-label" style="left:484px;top:1410px">Big Discount</div>
<div class="abs feat-label" style="left:812px;top:1414px">Experience Officials</div>

<div class="abs btn btn-fill" style="left:440px;top:1465px;width:150px;height:52px">Know More</div>
<div class="abs btn btn-line" style="left:610px;top:1463px;width:151px;height:54px">Book Your Trip</div>

<div class="sh" style="left:147px;top:1573px">
  <h2>New Villas and Vacation Rentals</h2>
  <div class="rule" style="margin-left:348px;width:256px"></div>
  <em style="margin-left:365px">Feel the Heaven</em>
</div>
<div class="abs arrow prev" style="left:946px;top:1588px">&lt;</div>
<div class="abs arrow next" style="left:1010px;top:1588px">&gt;</div>

<article class="abs villa" style="left:152px">
  <div class="photo" role="img" aria-label="Photo of a stone villa with white pergola and swimming pool" style="background:linear-gradient(180deg,#7fb2e0 0%,#d8cfc0 50%,#26b7d6 100%)"></div>
  <div class="body"><h3>Villa 1</h3><div class="loc">Itri</div>
    <div class="rate"><span class="stars">★★★★★</span><span class="rev">11 reviews</span></div>
    <div class="desc">Facility of Swimming pool and Parking</div><div class="more">More Details</div></div>
  <div class="specs"><span>Sleeps: 12</span><span>Bedrooms: 6</span><span>Bathrooms: 5</span><span>Floor Area: 300 m2</span></div>
</article>
<article class="abs villa" style="left:462px">
  <div class="photo" role="img" aria-label="Photo of an orange farmhouse villa with pool" style="background:linear-gradient(180deg,#8ab8e8 0%,#d9793e 45%,#3fa9c8 100%)"></div>
  <div class="body"><h3>Agriturismo Il Sole</h3><div class="loc">Tuscany</div>
    <div class="rate"><span class="stars">★★★★<s>★</s></span><span class="rev">57 reviews</span></div>
    <div class="desc">Facility of Cycling and Adventure Programs</div><div class="more">More Details</div></div>
  <div class="specs"><span>Sleeps: 12</span><span>Bedrooms: 6</span><span>Bathrooms: 5</span><span>Floor Area: 300 m2</span></div>
</article>
<article class="abs villa" style="left:775px">
  <div class="photo" role="img" aria-label="Photo of a modern white villa with palm trees and pool" style="background:linear-gradient(180deg,#9fb8cf 0%,#d6d0c2 45%,#1e9fc6 100%)"></div>
  <div class="body"><h3>Agriturismo Il Bianco</h3><div class="loc">Tuscany</div>
    <div class="rate"><span class="stars">★★★<s>★★</s></span><span class="rev">567 reviews</span></div>
    <div class="desc">Facility of Natural Surrounding</div><div class="more">More Details</div></div>
  <div class="specs"><span>Sleeps: 12</span><span>Bedrooms: 6</span><span>Bathrooms: 5</span><span>Floor Area: 300 m2</span></div>
</article>

<div class="sh" style="left:147px;top:2053px">
  <h2>Testimonials</h2>
  <div class="rule" style="margin-left:30px;width:224px"></div>
  <em style="margin-left:47px">Join the community of our happy users</em>
</div>
<div class="abs arrow prev" style="left:946px;top:2064px">&lt;</div>
<div class="abs arrow next" style="left:1010px;top:2064px">&gt;</div>
<div class="abs quote-deco" aria-hidden="true">“”</div>

<div class="abs tbox" style="left:154px">“Lorem ipsum dolor sit amet, consectetur adipiscing elit, sed do eiusmod tempor incididunt ut labore et dolore magna aliqua. Quis ipsum suspendisse ultrices gravida. Risus commodo viverra maecenas accumsan vel facilisis.”</div>
<div class="abs tbox" style="left:617px">“Lorem ipsum dolor sit amet, consectetur adipiscing elit, sed do eiusmod tempor incididunt ut labore et dolore magna aliqua. Quis ipsum suspendisse ultrices gravida. Risus commodo viverra maecenas accumsan vel facilisis.”</div>
<div class="abs avatar" style="left:329px;top:2159px;background:linear-gradient(180deg,#7a3a2a,#2a1a18)" role="img" aria-label="Portrait photo of a customer"></div>
<div class="abs avatar" style="left:793px;top:2159px;background:linear-gradient(180deg,#6aa4c8,#3a4a3a)" role="img" aria-label="Portrait photo of a customer"></div>

<div class="abs footer-band" role="img" aria-label="Photo of snowy mountain peaks tinted blue to orange"></div>

<form class="abs news">
  <h4>Get New offers and Updates</h4>
  <div class="email">Email</div>
  <div class="submit">Submit</div>
</form>

<div class="abs fcol" style="left:150px">
  <h5>Follow Us</h5>
  <ul><li><span class="sq"></span>Like Us</li><li><span class="sq"></span>Follow us</li><li><span class="sq"></span>Follow Us</li></ul>
</div>
<div class="abs fcol" style="left:463px">
  <h5>Company</h5>
  <ul><li>Privacy Policies</li><li class="hl">Reservation Policies</li><li>Cookie Policy</li></ul>
</div>
<div class="abs fcol contact" style="left:783px">
  <h5 class="light">Tripnesta</h5>
  <ul>
    <li><svg width="18" height="24" viewBox="0 0 18 24"><path d="M9 1a7.5 7.5 0 0 0-7.5 7.5C1.5 14 9 23 9 23s7.5-9 7.5-14.5A7.5 7.5 0 0 0 9 1z" fill="#fff"/><circle cx="9" cy="8.5" r="3" fill="#c98a7a"/></svg><span>via dei Ciliegi 7<br>50100 Borgo Sereno, Siena (Italy)</span></li>
    <li><svg width="22" height="22" viewBox="0 0 24 24"><path d="M6.6 10.8a15 15 0 0 0 6.6 6.6l2.2-2.2c.3-.3.7-.4 1-.2 1.1.4 2.3.6 3.6.6.6 0 1 .4 1 1V20c0 .6-.4 1-1 1A17 17 0 0 1 3 4c0-.6.4-1 1-1h3.5c.6 0 1 .4 1 1 0 1.3.2 2.5.6 3.6.1.3 0 .7-.2 1z" fill="#fff"/></svg><span style="margin-top:4px">Phone: +39 000 1234567</span></li>
    <li><svg width="22" height="22" viewBox="0 0 22 22"><circle cx="11" cy="11" r="9.5" fill="none" stroke="#fff" stroke-width="2"/><path d="M1.5 11h19M11 1.5c-5 5-5 14 0 19M11 1.5c5 5 5 14 0 19" fill="none" stroke="#fff" stroke-width="1.5"/></svg><span style="margin-top:4px">VAT Code: IT00000000000</span></li>
  </ul>
</div>

<div class="abs copyright">Copyright © 2021 Tripnesta. All Rights Reserved. Powered by Tripnesta</div>

</body>
</html>
```